Attic Lanterns (Progressive House Album)

Hey Guys,

I'm a music artist and I need a CD Cover done for my new album.The album is called "Attic Lanterns" and I really need something artistic, almost like a painting that reflects the name of the album.

Also please feel free to step out from the whole "almost like a painting" box, if your inner creator has something else to say. But preferably I'd have it as a painting...

Here are some keywords: Deep, Progressive, Lucid Dreaming, Ocean, Bedroom...

Please listen to the 3:30 demo of the album to get a better idea.

Thanks,

ToLa

Update:

I've uploaded a few images to kinda help you with the mood/colour tone and direction of what I want, Also, the script writing (I've uploaded a few examples), do it in white colour (left to right, going little bit upwards), preferably on the bottom of the image, simple, one touch, thin hand writing. Have it fading in size (bigger to smaller) as you get to the end of each word. Just like when you sign something, but have it written in two lines.

The whole image should be deep in colour with sort of a glow effect.

Must have
• Name of the album with Script writing,
Should not have
• No paper mosaic art. Image pieced together with cut outs from different sources.

```html
<!DOCTYPE html>
<html lang="en">
<head>
<meta charset="utf-8">
<title>Attic Lanterns – Album Cover</title>
<link href="https://fonts.googleapis.com/css2?family=Pinyon+Script&display=swap" rel="stylesheet">
<style>
  :root {
    --page: #ffffff;
    --violet: #5a3fb8;
    --indigo: #3b3fa8;
    --cyan: #52c8ee;
    --magenta: #c048c8;
    --rose: #e07aa0;
    --lilac: #b9a6e6;
    --ink: #ffffff;
  }
  html, body {
    margin: 0;
    width: 1200px;
    height: 1200px;
    overflow: hidden;
    background: var(--page);
  }
  .canvas {
    position: relative;
    width: 1200px;
    height: 1200px;
    background: var(--page);
  }
  .cover {
    position: absolute;
    left: 120px;
    top: 120px;
    width: 960px;
    height: 960px;
    overflow: hidden;
    box-shadow: 0 0 2px rgba(40, 30, 80, 0.5);
  }
  .cover-art {
    position: absolute;
    inset: 0;
    background:
      radial-gradient(circle at 50% 20%, rgba(224, 122, 160, 0.75) 0, transparent 32%),
      radial-gradient(circle at 15% 30%, rgba(82, 200, 238, 0.7) 0, transparent 28%),
      radial-gradient(circle at 85% 35%, rgba(82, 200, 238, 0.6) 0, transparent 26%),
      radial-gradient(circle at 20% 75%, rgba(192, 72, 200, 0.55) 0, transparent 30%),
      radial-gradient(circle at 80% 80%, rgba(90, 63, 184, 0.8) 0, transparent 32%),
      radial-gradient(circle at 50% 55%, rgba(59, 63, 168, 0.85) 0, transparent 34%),
      radial-gradient(circle at 10% 5%, rgba(59, 63, 168, 0.9) 0, transparent 22%),
      radial-gradient(circle at 90% 5%, rgba(90, 63, 184, 0.9) 0, transparent 22%),
      linear-gradient(135deg, var(--lilac), var(--magenta) 45%, var(--indigo));
  }
  .album-title {
    position: absolute;
    inset: 0;
    margin: 0;
    font-family: "Pinyon Script", cursive;
    font-weight: 400;
    color: var(--ink);
    text-shadow: 0 0 14px rgba(40, 20, 90, 0.35);
  }
  .album-title .line {
    position: absolute;
    white-space: nowrap;
    line-height: 1;
  }
  .album-title .line-one {
    left: 120px;
    top: 230px;
    font-size: 190px;
  }
  .album-title .line-two {
    left: 250px;
    top: 380px;
    font-size: 190px;
  }
</style>
</head>
<body>
  <main class="canvas">
    <section class="cover">
      <div class="cover-art" role="img" aria-label="Fluid marbled painting in violet, cyan and rose with translucent reaching hands around a central starburst"></div>
      <h1 class="album-title">
        <span class="line line-one">Attic</span>
        <span class="line line-two">Lanterns</span>
      </h1>
    </section>
  </main>
</body>
</html>
```